Fenlow Systems

Looking for a web site design to market our services/applications
We write and supply bespoke web applications for the offshore and construction industries
Our initial product is Tolv - rope access equipment management
Our buyers will be Rope Access companies via trade associations such as KOBEN and DULMO
we have a logo designed see it attached we would like to see crisp professional designs based around these colours and design
we will supply web copy later
looking for home, services, blog, contact us, order and a general template (privacy, site map, T&C) pages
Updates
This payment will be for the homepage only
We can discuss other options (pages) with the successful designer
Regards
Marcus
Industry/Entity Type
Construction
Look and feel
Each slider illustrates characteristics of the customer's brand and the style your logo design should communicate.

```html
<!DOCTYPE html>
<html lang="en">
<head>
<meta charset="utf-8">
<title>Fenlow Systems</title>
<link href="https://fonts.googleapis.com/css2?family=Open+Sans:wght@400;600&family=Roboto:wght@300;400&display=swap" rel="stylesheet">
<style>
:root{
  --sky:#1a9ad6;
  --navy:#0e2d7d;
  --text:#3a3a3a;
  --muted:#666;
  --line:#d8d8d8;
  --footer:#1d1d1f;
  --btn-top:#3bb7ea;
  --btn-bottom:#1494d3;
}
*{margin:0;padding:0;box-sizing:border-box}
html,body{width:984px;height:1200px;overflow:hidden;background:#fff}
body{position:relative;font-family:"Open Sans",sans-serif;color:var(--text)}
.abs{position:absolute}
.topline{top:0;left:0;width:984px;height:3px;background:linear-gradient(90deg,var(--navy) 50%,var(--sky) 50%)}
.brand{left:107px;top:20px;display:flex;align-items:center;gap:10px}
.brand-mark{width:46px;height:46px;border-radius:6px;background:#eceef1}
.brand-divider{width:1px;height:68px;background:var(--line);margin-left:6px}
.brand-name{font-family:"Roboto",sans-serif;font-size:19px;line-height:20px;color:var(--navy)}
.nav{left:375px;top:37px;display:flex;gap:39px;font-size:13px;color:#333}
.nav a{color:inherit;text-decoration:none;padding-bottom:5px}
.nav a.active{border-bottom:2px solid var(--sky)}
.search{left:862px;top:36px}
.hero{left:0;top:86px;width:984px;height:362px;background:linear-gradient(180deg,#dfe6f0 0%,#b8c6d9 60%,#9fb0c6 100%)}
.arrow{top:233px}
.caption{left:107px;top:376px;width:770px;height:72px;background:rgba(40,40,40,.82);display:flex;align-items:center;justify-content:space-between;padding:0 23px}
.caption h2{font-family:"Roboto",sans-serif;font-weight:300;font-size:28px;color:#fff}
.caption .outline-btn{border:2px solid #fff;color:#fff;font-family:"Roboto",sans-serif;font-weight:300;font-size:16px;width:130px;height:31px;line-height:27px;text-align:center}
.title{font-family:"Roboto",sans-serif;font-weight:400;font-size:24px;color:var(--sky);white-space:nowrap}
.title b{font-weight:400;color:var(--navy)}
p.copy{font-size:11px;line-height:20px;color:var(--text)}
.btn{width:115px;height:33px;background:linear-gradient(var(--btn-top),var(--btn-bottom));color:#fff;font-family:"Roboto",sans-serif;font-weight:300;font-size:15px;text-align:center;line-height:33px}
.photo{background:linear-gradient(135deg,#5d6f84,#9aa9b8)}
.news-title{font-family:"Roboto",sans-serif;font-weight:400;font-size:18px;color:var(--navy);white-space:nowrap}
.news-date{font-size:11px;color:var(--navy)}
.more{font-size:11px;color:var(--text)}
.field{width:343px;height:39px;border:1px solid var(--line);font-size:11px;color:#777;padding:0 11px;line-height:37px}
.footer{left:0;top:1091px;width:984px;height:109px;background:var(--footer)}
.footer-copy{left:107px;top:1112px;font-size:12px;color:#fff}
.footer-links{left:642px;top:1111px;font-size:12px;color:#fff;display:flex;gap:20px}
</style>
</head>
<body>
<div class="abs topline"></div>

<header>
  <div class="abs brand">
    <div class="brand-mark"></div>
    <div class="brand-divider"></div>
    <div class="brand-name">Fenlow<br>Systems</div>
  </div>
  <nav class="abs nav">
    <a class="active">Home</a><a>About Us</a><a>Services</a><a>Blog</a><a>Order</a><a>Contact us</a>
  </nav>
  <svg class="abs search" width="16" height="16" viewBox="0 0 16 16"><circle cx="6.5" cy="6.5" r="5" fill="none" stroke="var(--sky)" stroke-width="2.2"/><line x1="10" y1="10" x2="14.5" y2="14.5" stroke="var(--sky)" stroke-width="2.6" stroke-linecap="round"/></svg>
</header>

<section class="abs hero" role="img" aria-label="Two engineers in hard hats talking in front of office towers"></section>
<svg class="abs arrow" style="left:11px" width="46" height="46" viewBox="0 0 46 46"><circle cx="23" cy="23" r="21.5" fill="none" stroke="#fff" stroke-width="2"/><polyline points="26,14 18,23 26,32" fill="none" stroke="#fff" stroke-width="2.5"/></svg>
<svg class="abs arrow" style="left:926px" width="46" height="46" viewBox="0 0 46 46"><circle cx="23" cy="23" r="21.5" fill="none" stroke="#fff" stroke-width="2"/><polyline points="20,14 28,23 20,32" fill="none" stroke="#fff" stroke-width="2.5"/></svg>
<div class="abs caption">
  <h2>TOLV - Rope access equipment management</h2>
  <div class="outline-btn">View Details</div>
</div>

<section>
  <h2 class="abs title" style="left:107px;top:472px">Welcome To Fenlow <b>Systems</b></h2>
  <p class="abs copy" style="left:107px;top:511px;width:332px">Lorem ipsum dolor sit amet, et his malorum pertinax. Eam utroque probatus cu, sit cu esse perpetua philosophia, fugit mollis ei has. Qui cu mollis nostrud vocibus. His nobis commune ullamcorper ea. Mea inani sanctus mandamus no.</p>
  <p class="abs copy" style="left:107px;top:600px;width:332px">Ex quas etiam lucilius est, eius pertinax in vix. Eu vel vide menti-tum. Veri omnesque his cu, cum mucius nostrum probatus ut, mea rebum ullum voluptua ut.</p>
  <div class="abs btn" style="left:108px;top:676px">Read More</div>
</section>

<section>
  <h2 class="abs title" style="left:485px;top:472px">Rope access equipment <b>management</b></h2>
  <div class="abs photo" style="left:486px;top:517px;width:148px;height:92px" role="img" aria-label="Rope access technician working on a glass building facade"></div>
  <p class="abs copy" style="left:657px;top:512px;width:224px">Ne nec harum feugiat, causae mandamus argumentum te vel, intellegat definiebas ut sea. Ad pro brute phaedrum, quas tamquam id eam.Ne nec harum feugiat, causae mandamus argumentum te vel.</p>
  <p class="abs copy" style="left:486px;top:622px;width:394px">Ex eam ipsum everti gubergren, vis justo dicta eruditi eu. Ex eam ipsum ever-bergren, vis justo dicta eruditi eu.</p>
  <div class="abs btn" style="left:487px;top:676px">Read More</div>
</section>

<section>
  <h2 class="abs title" style="left:106px;top:739px">Latest <b>News</b></h2>
  <div class="abs photo" style="left:108px;top:786px;width:102px;height:84px;background:linear-gradient(135deg,#d8dde6,#4b7fc0)" role="img" aria-label="Worker in a hard hat on a ladder"></div>
  <h3 class="abs news-title" style="left:235px;top:780px">Lorem ipsum dolor</h3>
  <div class="abs news-date" style="left:236px;top:813px">April 23, 2014</div>
  <p class="abs copy" style="left:235px;top:835px;width:176px">Ex quas etiam lucilius est, eius perti-nax in vix. Eu vel vide mentitum.</p>
  <div class="abs more" style="left:413px;top:855px">[···]</div>

  <div class="abs photo" style="left:108px;top:896px;width:102px;height:84px;background:linear-gradient(135deg,#f1ede6,#c9b08e)" role="img" aria-label="House model with plans and a calculator"></div>
  <h3 class="abs news-title" style="left:235px;top:890px">Lorem ipsum dolor</h3>
  <div class="abs news-date" style="left:236px;top:924px">May 12, 2014</div>
  <p class="abs copy" style="left:235px;top:946px;width:176px">Ex quas etiam lucilius est, eius perti-nax in vix. Eu vel vide mentitum.</p>
  <div class="abs more" style="left:413px;top:966px">[···]</div>
  <div class="abs btn" style="left:108px;top:1006px">View All</div>
</section>

<section>
  <h2 class="abs title" style="left:485px;top:739px">Contact <b>Us</b></h2>
  <p class="abs copy" style="left:486px;top:779px;width:390px">Ne nec harum feugiat, causae mandamus argumentum te vel, intellegat definiebas ut sea. Ad pro brute phaedrum, quas tamquam id eam.</p>
  <div class="abs field" style="left:486px;top:835px">Enter Your Name...</div>
  <div class="abs field" style="left:486px;top:889px">Enter Your Email...</div>
  <div class="abs field" style="left:486px;top:943px">Enter Your Message...</div>
  <div class="abs btn" style="left:487px;top:1006px">Submit</div>
</section>

<footer>
  <div class="abs footer"></div>
  <div class="abs footer-copy">Copyright @ 2014 Fenlowsystems.All Rights Reserved.</div>
  <div class="abs footer-links"><span>Privacy</span><span>|</span><span>SitemapPrivacy</span><span>|</span><span>T&amp;C</span></div>
  <svg class="abs" style="left:107px;top:1151px" width="88" height="22" viewBox="0 0 88 22">
    <circle cx="11" cy="11" r="10.5" fill="#3a3a3d"/><circle cx="43" cy="11" r="10.5" fill="#3a3a3d"/><circle cx="75" cy="11" r="10.5" fill="#3a3a3d"/>
  </svg>
  <svg class="abs" style="left:737px;top:1143px" width="140" height="36" viewBox="0 0 140 36">
    <rect x="2" y="6" width="60" height="24" rx="3" fill="#8a8a8a"/>
    <ellipse cx="113" cy="18" rx="25" ry="17" fill="#8a8a8a"/>
  </svg>
</footer>
</body>
</html>
```